Venture 482 - Lumora Book Cover

I am looking for a Lumora book cover for my book about "Venture 482".
The Book is Titled:
Venture 482 Ascended
Shaping Outcomes: Paths To Unlocking Cosmic Truths
Author is Dorian Pell
Here is a book description that may help you understand more about it:
Inspired by the genius of Edwin Marlowe, this comprehensive guide delves into the ancient wisdom and cutting-edge science behind the 482 method, a powerful tool for manifesting your desires. Whether you're seeking personal growth, financial success, or spiritual enlightenment, this book provides advanced techniques and methods to transform your dreams into reality.
Any questions please ask.
Thanks
Owen

```html
<!DOCTYPE html>
<html lang="en">
<head>
<meta charset="utf-8">
<title>Venture 482 Ascended — Dorian Pell</title>
<link rel="stylesheet" href="https://fonts.googleapis.com/css2?family=Cinzel:wght@400;700&family=DM+Serif+Display&family=Sora:wght@700&family=Tenor+Sans&family=Tinos&display=swap">
<style>
  :root {
    --page-bg: #e6e6e4;
    --art-top: #06101f;
    --art-upper: #163a63;
    --art-middle: #2f6a98;
    --art-lower: #1d4670;
    --art-bottom: #0f2342;
    --title-cream: #fde9dc;
    --subtitle-cream: #fbf3d8;
    --shadow-ink: #0a1424;
    --body-white: #f4f1ec;
  }
  html, body {
    margin: 0;
    width: 1200px;
    height: 1131px;
    overflow: hidden;
    background: var(--page-bg);
  }
  .book-cover {
    position: absolute;
    left: 246px;
    top: 30px;
    width: 707px;
    height: 1071px;
    overflow: hidden;
  }
  .cover-art {
    position: absolute;
    inset: 0;
    background: linear-gradient(180deg,
      var(--art-top) 0%,
      var(--art-upper) 28%,
      var(--art-middle) 55%,
      var(--art-lower) 78%,
      var(--art-bottom) 100%);
  }
  .cover-type {
    position: absolute;
    inset: 0;
    width: 100%;
    height: 100%;
  }
  .author-name {
    font-family: "Cinzel", serif;
    font-size: 46px;
    fill: var(--title-cream);
  }
  .title-word {
    font-family: "Sora", sans-serif;
    font-weight: 700;
    font-size: 90px;
    fill: var(--title-cream);
  }
  .title-number {
    font-family: "DM Serif Display", serif;
    font-size: 284px;
    fill: var(--title-cream);
  }
  .edition-label {
    font-family: "Cinzel", serif;
    font-weight: 700;
    font-size: 52px;
    fill: var(--subtitle-cream);
  }
  .subtitle-heading {
    font-family: "Tenor Sans", sans-serif;
    font-size: 31px;
    fill: var(--body-white);
  }
  .subtitle-line {
    font-family: "Tinos", serif;
    font-size: 25px;
    fill: var(--body-white);
  }
</style>
</head>
<body>
  <main class="book-cover">
    <div class="cover-art" role="img" aria-label="Cover illustration: a lone figure in a tall doorway on a still lake at dusk, with red-blossomed trees and distant mountains"></div>

    <svg class="cover-type" viewBox="0 0 707 1071">
      <defs>
        <filter id="edition-shadow" x="-10%" y="-30%" width="120%" height="160%">
          <feDropShadow dx="3" dy="3" stdDeviation="1" flood-color="var(--shadow-ink)" flood-opacity="0.9"/>
        </filter>
        <filter id="title-shadow" x="-10%" y="-20%" width="120%" height="140%">
          <feDropShadow dx="2" dy="3" stdDeviation="3" flood-color="var(--shadow-ink)" flood-opacity="0.55"/>
        </filter>
      </defs>
      <text class="author-name" x="376" y="103" text-anchor="middle" textLength="549" lengthAdjust="spacing">DORIAN PELL</text>
      <text class="title-word" x="361" y="229" text-anchor="middle" textLength="463" lengthAdjust="spacingAndGlyphs" filter="url(#title-shadow)">VENTURE</text>
      <text class="title-number" x="364" y="444" text-anchor="middle" textLength="515" lengthAdjust="spacingAndGlyphs" filter="url(#title-shadow)">482</text>
      <text class="edition-label" x="363" y="517" text-anchor="middle" textLength="493" lengthAdjust="spacing" filter="url(#edition-shadow)">ASCENDED</text>
      <text class="subtitle-heading" x="356" y="948" text-anchor="middle" textLength="396" lengthAdjust="spacingAndGlyphs">SHAPING OUTCOMES:</text>
      <text class="subtitle-line" x="356" y="994" text-anchor="middle" textLength="263" lengthAdjust="spacingAndGlyphs">Paths to unlocking</text>
      <text class="subtitle-line" x="356" y="1027" text-anchor="middle" textLength="182" lengthAdjust="spacingAndGlyphs">cosmic truths</text>
    </svg>
  </main>
</body>
</html>
```